Manifesto

I want a manifesto with the following five manifestos for our Not for Profit

- We are a For-purpose organisation
- Every service we offer is free
- Every product we sell funds our services
- Every financial transaction is transparent
- Our service is for the greater good
- Our purpose is always to serve the people
- We are a for purpose organisation

Its to go with this website logo/look/feel www.brightharbour.co.nz

Two attachments:

1. I quite like this look/feel of a manifesto (see attached), I want something clean, professional but I also quite like either Retro modern look feel also like a fresh, and uplifting as its for sick people coming to see us and our funds where anyone buys a product are used for helping those who are sick with healing......so needs something conveyed that is fresh, uplifing yet professional.
2. This attachment is how I wrote this down when inspired of how I wanted Bright Harbour to operate. This is our values chart. It has to say

Also check out our website for our logo, look etc.. it doesnt have to be the same but red somewhere would link back to logo. www.brightharbour.co.nz .

Industry/Entity Type

Financial

```html
<!DOCTYPE html>
<html lang="en">
<head>
<meta charset="utf-8">
<title>Bright Harbour Manifesto</title>
<link rel="stylesheet" href="https://fonts.googleapis.com/css2?family=Rokkitt:wght@800;900&family=Lobster&family=Questrial&display=swap">
<style>
  :root {
    --backdrop: #e9e9e9;
    --backdrop-edge: #cfcfcf;
    --poster-red: #98001c;
    --poster-red-deep: #5c0010;
    --ink-dark: #4a0812;
    --ink-light: #ffffff;
    --shadow: #2a0008;
  }
  html, body {
    margin: 0;
    padding: 0;
    width: 1200px;
    height: 1000px;
    overflow: hidden;
    background: radial-gradient(ellipse at center, var(--backdrop) 55%, var(--backdrop-edge) 100%);
  }
  .manifesto {
    display: block;
    width: 1200px;
    height: 1000px;
  }
  .slab {
    font-family: "Rokkitt", "Rockwell", serif;
    font-weight: 900;
  }
  .script {
    font-family: "Lobster", cursive;
  }
  .geometric {
    font-family: "Questrial", sans-serif;
    font-weight: 700;
  }
  .ink-dark { fill: var(--ink-dark); }
  .ink-light { fill: var(--ink-light); filter: url(#lift); }
  .divider { fill: var(--ink-dark); }
</style>
</head>
<body>
<svg class="manifesto" viewBox="0 0 1200 1000" xmlns="http://www.w3.org/2000/svg">
  <defs>
    <radialGradient id="poster-vignette" cx="50%" cy="50%" r="70%">
      <stop offset="55%" stop-color="var(--poster-red)"/>
      <stop offset="100%" stop-color="var(--poster-red-deep)"/>
    </radialGradient>
    <filter id="lift" x="-5%" y="-10%" width="115%" height="130%">
      <feDropShadow dx="2" dy="3" stdDeviation="0.6" flood-color="#2a0008" flood-opacity="0.9"/>
    </filter>
    <filter id="poster-shadow" x="-5%" y="-5%" width="110%" height="110%">
      <feDropShadow dx="0" dy="2" stdDeviation="3" flood-color="#000" flood-opacity="0.25"/>
    </filter>
  </defs>

  <rect class="poster" x="277" y="41" width="648" height="917" fill="url(#poster-vignette)" filter="url(#poster-shadow)"/>

  <!-- Value: for-purpose -->
  <g class="value value-purpose">
    <text class="slab ink-dark" x="300" y="120" font-size="62" textLength="315" lengthAdjust="spacingAndGlyphs">WE ARE A</text>
    <text class="slab ink-light" x="300" y="164" font-size="46" textLength="315" lengthAdjust="spacingAndGlyphs">FOR PURPOSE</text>
    <text class="slab ink-dark" x="300" y="210" font-size="40" textLength="315" lengthAdjust="spacingAndGlyphs">ORGANISATION</text>
  </g>

  <!-- Value: free service -->
  <g class="value value-free">
    <text class="script ink-light" x="657" y="105" font-size="42" textLength="243" lengthAdjust="spacingAndGlyphs">Every Service</text>
    <text class="slab ink-dark" x="660" y="138" font-size="26" textLength="240" lengthAdjust="spacing">we offer is</text>
    <text class="slab ink-dark" x="660" y="208" font-size="86" textLength="240" lengthAdjust="spacingAndGlyphs">FREE</text>
  </g>

  <path class="divider" d="M330,230 Q599,225 868,230 Q599,235 330,230 Z"/>

  <!-- Value: products fund services -->
  <g class="value value-products">
    <text class="slab ink-light" x="300" y="300" font-size="68" textLength="600" lengthAdjust="spacingAndGlyphs">EVERY PRODUCT</text>
    <text class="slab ink-dark" x="300" y="345" font-size="42" textLength="600" lengthAdjust="spacingAndGlyphs">we sell funds our services</text>
  </g>

  <path class="divider" d="M330,368 Q599,363 868,368 Q599,373 330,368 Z"/>

  <!-- Value: transparency -->
  <g class="value value-transparency">
    <text class="slab ink-light" x="300" y="440" font-size="54" textLength="275" lengthAdjust="spacing">EVERY</text>
    <text class="slab ink-light" x="300" y="480" font-size="32" textLength="275" lengthAdjust="spacing">FINANCIAL</text>
    <text class="slab ink-dark" x="300" y="516" font-size="30" textLength="275" lengthAdjust="spacing">TRANSACTION</text>
    <text class="slab ink-dark" x="300" y="545" font-size="28" textLength="275" lengthAdjust="spacing">is transparent</text>
  </g>

  <!-- Value: greater good -->
  <g class="value value-good">
    <text class="slab ink-dark" x="622" y="420" font-size="30" textLength="278" lengthAdjust="spacing">OUR SERVICE IS</text>
    <text class="script ink-light" x="625" y="467" font-size="46" textLength="275" lengthAdjust="spacingAndGlyphs">for the greater</text>
    <text class="geometric ink-light" x="632" y="543" font-size="90" textLength="268" lengthAdjust="spacingAndGlyphs">GOOD</text>
  </g>

  <path class="divider" d="M330,574 Q599,569 868,574 Q599,579 330,574 Z"/>

  <!-- Value: serve the people -->
  <g class="value value-people">
    <text class="slab ink-dark" x="300" y="648" font-size="62" textLength="600" lengthAdjust="spacing">OUR PURPOSE IS</text>
    <text class="script ink-light" x="300" y="697" font-size="52" textLength="600" lengthAdjust="spacingAndGlyphs">always to serve the people</text>
  </g>

  <path class="divider" d="M330,738 Q599,733 868,738 Q599,743 330,738 Z"/>

  <!-- Closing statement -->
  <g class="value value-closing">
    <text class="slab ink-dark" x="300" y="795" font-size="48" textLength="605" lengthAdjust="spacingAndGlyphs">WE ARE A FOR PURPOSE</text>
    <text class="script ink-light" x="298" y="888" font-size="116" textLength="602" lengthAdjust="spacingAndGlyphs">organisation</text>
  </g>
</svg>
</body>
</html>
```